Small legal and financial translation company needs Squarespace website, brochure and logo

Hello,
We are Lumarin Services (www.lumarinservices-example.com), a boutique legal and financial translation company. We offer our services mainly to Spanish customers. Our primary line of business is the translation of financial statements, but we translate a wide variety legal and financial texts.
The project we are offering comprises three parts: a redo of the current website, an informational brochure for potential customer and a logo design. These three parts should provide a consistent image. We would develop content soon.
We are looking for a website that would look like a typical law firm website, nothing too fancy. Right now, it is in English, Spanish and French, although the new site need only be in English and Spanish. There must be good toggling between the English and Spanish versions. There would be no need for tie-ins to social media and it would not contain a blog. Basically, a static site. We aren't interesting in driving traffic to the site or SEO, as we will contact nearly all potential customers beforehand. The website must be built in Squarespace to enable a smooth transition. The content would be similar to the current page, we'll be working on the exact content, but a rough draft is attached.
The brochure will be some three pages and would introduce the company to potential customers, using similar images as the website and the logo to be designed.
The only specifications for the logo is, as the website and brochure, it convey a sense of security and trust.
Feel free to ask with any questions as this is the first time we have used this platform.
Thank you!
Updates

I've added a more or less final version for the text in the brochure and updated the brief. Added Wednesday, June 10, 2015

Target Market(s)

Spanish law firms, auditors, accountants, banks, investment firms

Industry/Entity Type

Finance

Logo Text

Lumarin Services

Number of Pages Required

5+ page

Font styles to use
Serif

Requirements
Must have
• The website must be built in Squarespace and have a good option to toggle between English and Spanish versions.
• Brochure must be in both English and Spanish, I'm attaching a rough draft of the information that it will probably have. This should give an idea about what to include and the spacing. I will update it to include the final information.
Nice to have
• Would be nice to have some quality finance- and legal-related images
Should not have
• Vibrant colours

```html
<!DOCTYPE html>
<html lang="en">
<head>
<meta charset="utf-8">
<title>Lumarin Services – Brochure Spread</title>
<link rel="stylesheet" href="https://fonts.googleapis.com/css2?family=Cinzel:wght@400&family=Crimson+Text:wght@400&family=Open+Sans:wght@400&display=swap">
<style>
  :root {
    --stage: #c8c8c8;
    --label: #555555;
    --maroon: #7b0011;
    --ink: #1a1a1a;
    --paper: #ffffff;
    --night: #000000;
    --photo-light: #bdbdbd;
    --photo-dark: #3a3a3a;
  }
  * { margin: 0; padding: 0; box-sizing: border-box; }
  html, body { width: 1200px; height: 1066px; overflow: hidden; }
  body { background: var(--stage); position: relative; font-family: "Crimson Text", Georgia, serif; color: var(--ink); }

  .page-label { position: absolute; top: 46px; width: 200px; text-align: center; font-family: "Open Sans", Arial, sans-serif; font-size: 28px; color: var(--label); }
  .page-label--one { left: 236px; }
  .page-label--two { left: 783px; }

  .page { position: absolute; top: 108px; width: 550px; height: 849px; overflow: hidden; box-shadow: 0 4px 14px rgba(0,0,0,.35); }
  .page--intro { left: 54px; background: var(--paper); }
  .page--reasons { left: 604px; background: var(--night); color: var(--paper); }

  .section-title { position: absolute; font-family: "Cinzel", "Times New Roman", serif; font-size: 24px; letter-spacing: 1px; font-weight: 400; white-space: nowrap; }
  .page--intro .section-title { color: var(--maroon); }
  .page--reasons .section-title { color: var(--paper); }

  .team-photo { position: absolute; left: 26px; top: 84px; width: 238px; height: 209px; background: linear-gradient(120deg, var(--photo-light), #8a8a8a 45%, var(--photo-dark)); }

  .intro-text { position: absolute; left: 280px; top: 80px; width: 232px; font-size: 13.4px; line-height: 18.4px; text-align: justify; hyphens: auto; }
  .experience-text { position: absolute; left: 29px; top: 374px; width: 494px; font-size: 13.4px; line-height: 18.5px; text-align: justify; }

  .stat { position: absolute; top: 510px; width: 180px; text-align: center; }
  .stat__ring { width: 136px; height: 136px; margin: 0 auto; border: 2.5px solid var(--maroon); border-radius: 50%; display: flex; align-items: center; justify-content: center; font-size: 46px; line-height: 1; }
  .stat__label { margin-top: 12px; font-size: 13.5px; white-space: nowrap; }

  .footer-band { position: absolute; left: 0; bottom: 0; width: 550px; height: 102px; }
  .footer-url { position: absolute; left: 22px; top: 803px; font-size: 20px; color: var(--paper); letter-spacing: .2px; }

  .reason { position: absolute; left: 38px; width: 490px; }
  .reason__icon { position: absolute; left: 0; top: 0; width: 48px; height: 48px; }
  .reason__title { position: absolute; left: 67px; top: -10px; font-size: 18px; white-space: nowrap; }
  .reason__text { position: absolute; left: 68px; top: 16px; width: 415px; font-size: 12.8px; line-height: 15.6px; text-align: justify; }
</style>
</head>
<body>

<div class="page-label page-label--one">Page 1</div>
<div class="page-label page-label--two">Page 2</div>

<section class="page page--intro">
  <h2 class="section-title" style="left:25px; top:34px;">Who Are We?</h2>
  <div class="team-photo" role="img" aria-label="Black and white photo of a team of business professionals"></div>
  <p class="intro-text">We are a small, highly professional and qualified group of professionals with backgrounds in law, financial services and translation and interpretation that boasts experience in global consulting and auditing firms, law firms and companies from a cross section of industries. Sensitive to the workings of the financial world, we are detail-oriented experts striving to facilitate under-standing among investors, companies and international organisations.</p>

  <h2 class="section-title" style="left:30px; top:331px;">Experience You Can Trust On</h2>
  <p class="experience-text">Lorem ipsum dolor sit amet, consectetuer adipiscing elit, sed diam nonummy nibh euismod tincidunt ut laoreet dolore magna aliquam erat volutpat. Ut wisi enim ad minim veniam, quis nostrud exerci tation ullamcorper suscipit lobortis nisl ut aliquip ex ea commodo consequat. Duis autem vel eum iriure dolor in hendrerit in vulputate velit esse molestie consequat, vel illum dolore eu feugiat nulla facilisis at vero eros et accumsan et iusto odio.</p>

  <div class="stat" style="left:9px;"><div class="stat__ring">4589</div><p class="stat__label">Nos of Words Translated</p></div>
  <div class="stat" style="left:181px;"><div class="stat__ring">152</div><p class="stat__label">Nos of Documents Translated</p></div>
  <div class="stat" style="left:353px;"><div class="stat__ring">64</div><p class="stat__label">Nos of Satisfied Clients</p></div>

  <svg class="footer-band" viewBox="0 0 550 102" aria-hidden="true">
    <polygon points="0,0 550,102 0,102" fill="var(--maroon)"/>
    <polygon points="280,52 550,0 550,102" fill="var(--night)"/>
  </svg>
  <p class="footer-url">www.lumarinservices-example.com</p>
</section>

<section class="page page--reasons">
  <h2 class="section-title" style="left:39px; top:34px;">Why Choose Lumarin?</h2>

  <div class="reason" style="top:87px;">
    <svg class="reason__icon" viewBox="0 0 48 48" aria-hidden="true">
      <circle cx="24" cy="24" r="21.5" fill="none" stroke="#fff" stroke-width="2"/>
      <ellipse cx="24" cy="24" rx="10" ry="7.5" fill="#fff"/>
      <rect x="17" y="29" width="3" height="5" fill="#fff"/><rect x="27" y="29" width="3" height="5" fill="#fff"/>
      <rect x="21" y="17" width="6" height="2" fill="#000"/>
    </svg>
    <h3 class="reason__title" style="font-weight:400;">Save Money</h3>
    <p class="reason__text">Lorem ipsum dolor sit amet, consectetuer adipiscing elit, sed diam nonummy nibh euismod tincidunt ut laoreet dolore magna aliquam erat volutpat. Ut wisi enim ad minim veniam, quis nostrud exerci tation ullamcorper suscipit lobortis nisl ut aliquip ex ea commodo consequat.</p>
  </div>

  <div class="reason" style="top:220px;">
    <svg class="reason__icon" viewBox="0 0 48 48" aria-hidden="true">
      <circle cx="24" cy="24" r="21.5" fill="none" stroke="#fff" stroke-width="2"/>
      <polygon points="24,13 27,21 35.5,21.3 28.8,26.5 31.2,34.7 24,29.9 16.8,34.7 19.2,26.5 12.5,21.3 21,21" fill="#fff"/>
    </svg>
    <h3 class="reason__title" style="font-weight:400;">Quality Guaranteed</h3>
    <p class="reason__text">Lorem ipsum dolor sit amet, consectetuer adipiscing elit, sed diam nonummy nibh euismod tincidunt ut laoreet dolore magna aliquam erat volutpat. Ut wisi enim ad minim veniam, quis nostrud exerci tation ullamcorper suscipit lobortis nisl ut aliquip ex ea commodo consequat.</p>
  </div>

  <div class="reason" style="top:352px;">
    <svg class="reason__icon" viewBox="0 0 48 48" aria-hidden="true">
      <circle cx="24" cy="24" r="21.5" fill="none" stroke="#fff" stroke-width="2"/>
      <circle cx="21" cy="22" r="4" fill="#fff"/>
      <path d="M13 34 Q13 27 21 27 Q29 27 29 34 Z" fill="#fff"/>
      <circle cx="30" cy="15" r="4" fill="none" stroke="#fff" stroke-width="1.6"/>
    </svg>
    <h3 class="reason__title" style="font-weight:400;">Native Translators Only</h3>
    <p class="reason__text">Lorem ipsum dolor sit amet, consectetuer adipiscing elit, sed diam nonummy nibh euismod tincidunt ut laoreet dolore magna aliquam erat volutpat. Ut wisi enim ad minim veniam, quis nostrud exerci tation ullamcorper suscipit lobortis nisl ut aliquip ex ea commodo consequat.</p>
  </div>

  <div class="reason" style="top:484px;">
    <svg class="reason__icon" viewBox="0 0 48 48" aria-hidden="true">
      <circle cx="24" cy="24" r="21.5" fill="none" stroke="#fff" stroke-width="2"/>
      <path d="M33 24 A9 9 0 1 1 30 17" fill="none" stroke="#fff" stroke-width="2.4"/>
      <polygon points="28,13 33,17 27,19" fill="#fff"/>
      <path d="M24 19 V24 H28" fill="none" stroke="#fff" stroke-width="2"/>
    </svg>
    <h3 class="reason__title" style="font-weight:400;">Consistency Over Time</h3>
    <p class="reason__text">Lorem ipsum dolor sit amet, consectetuer adipiscing elit, sed diam nonummy nibh euismod tincidunt ut laoreet dolore magna aliquam erat volutpat. Ut wisi enim ad minim veniam, quis nostrud exerci tation ullamcorper suscipit lobortis nisl ut aliquip ex ea commodo consequat.</p>
  </div>

  <div class="reason" style="top:616px;">
    <svg class="reason__icon" viewBox="0 0 48 48" aria-hidden="true">
      <circle cx="24" cy="24" r="21.5" fill="none" stroke="#fff" stroke-width="2"/>
      <rect x="15" y="16" width="18" height="13" fill="none" stroke="#fff" stroke-width="2"/>
      <rect x="12" y="30" width="24" height="3" fill="#fff"/>
    </svg>
    <h3 class="reason__title" style="font-weight:400;">Use of Technology Helps Cut Costs</h3>
    <p class="reason__text">Lorem ipsum dolor sit amet, consectetuer adipiscing elit, sed diam nonummy nibh euismod tincidunt ut laoreet dolore magna aliquam erat volutpat. Ut wisi enim ad minim veniam, quis nostrud exerci tation ullamcorper suscipit lobortis nisl ut aliquip ex ea commodo consequat.</p>
  </div>

  <svg class="footer-band" viewBox="0 0 550 102" aria-hidden="true">
    <polygon points="0,0 550,100 550,102 0,102" fill="var(--maroon)"/>
    <line x1="0" y1="0" x2="550" y2="100" stroke="#fff" stroke-width="1.5"/>
  </svg>
  <p class="footer-url">www.lumarinservices-example.com</p>
</section>

</body>
</html>
```